Brenwick Structures Construction Company Seeking Modern Website

We are a small construction company wanting to create a web presence. We don't have much in the way of current content but will get photos as they come in. Attached is a picture of our business card.
The pages we would like on the menu are:
Home
Portfolio
Product Specs
Testimonials
Our Process
Contact
Some designs we like are:
http://www.tovasheds-example.com/
http://www.qrnstructures-example.com/
http://dunholtbarns-example.com/
http://pellingframes-example.com/
Not much requirements other than that so feel free to be creative!
Updates
Target Market(s)
Construction
Commercial and Residential Buildings
Industry/Entity Type
Construction Company
Number of Pages Required
5+ page
Look and feel

```html
<!DOCTYPE html>
<html lang="en">
<head>
<meta charset="utf-8">
<title>Brenwick Structures</title>
<link href="https://fonts.googleapis.com/css2?family=Roboto:ital,wght@0,300;0,400;0,500;0,700;1,400&display=swap" rel="stylesheet">
<style>
:root{
  --red:#d3302a;
  --red-btn:#d9332b;
  --blue:#1a93cb;
  --blue-dark:#1585b8;
  --ink:#333;
  --text:#5a5a5a;
  --muted:#777;
  --line:#d8d8d8;
  --gray-bg:#f1f1f1;
  --tab-dark:#4a4a4a;
  --footer:#2b2b2b;
  --white:#fff;
}
*{box-sizing:border-box;margin:0;padding:0}
html,body{width:1200px;height:2308px;overflow:hidden}
body{font-family:'Roboto',sans-serif;color:var(--text);background:var(--white);position:relative}
a{color:inherit;text-decoration:none}
.abs{position:absolute}

.top-rule{position:absolute;left:0;top:0;width:1200px;height:6px;background:var(--red)}
.header{position:absolute;left:0;top:6px;width:1200px;height:112px}
.contact-line{left:77px;top:51px;font-size:13px;color:var(--ink);display:flex;align-items:center;gap:8px}
.contact-line svg{width:12px;height:12px;fill:var(--ink)}
.contact-line .sep{margin:0 6px}
.brand{left:0;width:1200px;top:36px;text-align:center;font-size:32px;font-weight:700;color:var(--blue)}
.search{left:972px;top:43px;width:154px;height:34px;border:1px solid var(--line);font-size:11px;color:var(--muted);padding:11px 10px;display:flex;justify-content:space-between;align-items:center}
.search svg{width:13px;height:13px}

.nav{position:absolute;left:0;top:118px;width:1200px;height:44px;background:linear-gradient(var(--blue),var(--blue-dark));display:flex;justify-content:center;gap:50px;align-items:center}
.nav a{color:var(--white);font-size:13.5px;font-weight:500;letter-spacing:.3px}

.hero{position:absolute;left:0;top:162px;width:1200px;height:473px;overflow:hidden}
.hero-photo{position:absolute;inset:0;background:linear-gradient(90deg,#e6eef5 0%,#d6e4ef 40%,#8fa6bd 65%,#5f7a98 100%)}
.hero-title{left:75px;top:126px;font-size:40px;line-height:52px;font-weight:500;color:var(--blue);letter-spacing:1px}
.hero-sub{left:75px;top:232px;font-size:24px;color:#222}
.btn{display:inline-block;color:var(--white);font-weight:500;text-align:center}
.btn-red{background:var(--red-btn);border-radius:3px}
.hero .btn{left:75px;top:289px;width:160px;height:50px;line-height:50px;font-size:19px}

.welcome-title{left:0;width:1200px;top:676px;text-align:center;font-size:28px;font-weight:400;color:var(--red)}
.welcome-text{left:75px;width:1051px;top:730px;text-align:center;font-size:14.5px;line-height:27px}
.rule{left:75px;top:840px;width:1051px;height:2px;background:var(--line)}

.tabs{left:75px;top:878px;width:1051px;height:54px}
.tab-label{position:absolute;top:0;height:54px;line-height:54px;font-size:24px;color:var(--white)}
.service-box{left:75px;top:932px;width:1051px;height:406px;border:3px solid #444;border-top:none}
.service-photo{left:103px;top:995px;width:422px;height:283px;background:linear-gradient(160deg,#c9ccd0 0%,#9b9a96 45%,#5d554c 100%)}
.service-title{left:558px;top:988px;font-size:22px;font-weight:500;color:var(--red);letter-spacing:.4px}
.service-text{left:558px;top:1028px;width:508px;font-size:14px;line-height:27px}
.btn-blue{background:var(--blue)}
.service-btn{left:557px;top:1227px;width:160px;height:50px;line-height:50px;font-size:19px}

.updates{left:0;top:1377px;width:1200px;height:427px;background:var(--gray-bg)}
.sec-title{font-size:28px;color:var(--red);font-weight:400}
.blog-title{left:75px;top:1413px}
.post{position:absolute;top:1464px;width:242px}
.post-photo{width:242px;height:143px}
.post h3{margin-top:14px;font-size:12.5px;line-height:19px;font-weight:500;color:var(--blue)}
.post p{margin-top:8px;font-size:12.5px;line-height:21px}
.more{display:block;font-size:12.5px;font-weight:500;color:var(--red)}
.post .more{margin-top:11px}
.divider{left:857px;top:1420px;width:1px;height:333px;background:#ccc}
.news-title{left:884px;top:1413px}
.news-item{position:absolute;left:884px;width:240px}
.news-item .date{font-size:12.5px;font-weight:500;color:var(--blue)}
.news-item p{margin-top:5px;font-size:12.5px;line-height:21px}
.news-item .more{margin-top:5px}

.testi-title{left:0;width:1200px;top:1840px;text-align:center}
.testi-photo{left:165px;top:1896px;width:132px;height:130px;background:linear-gradient(#cfd3d8,#9aa0a7)}
.testi-quote{left:332px;top:1896px;width:710px;font-size:14px;line-height:27px;font-style:italic}
.qm{color:var(--red);font-weight:700;font-style:normal}
.testi-name{left:332px;top:2010px;font-size:14px;font-weight:500;color:var(--blue)}
.arrow{width:22px;height:28px}

.footer{left:0;top:2069px;width:1200px;height:239px;background:var(--footer)}
.footer-brand{left:82px;top:2138px;font-size:30px;font-weight:700;color:var(--blue)}
.footer-copy{left:76px;top:2201px;font-size:11.5px;line-height:22px;color:#bbb}
.fcol{position:absolute;top:2105px}
.fcol h4{font-size:16px;font-weight:500;color:var(--blue);letter-spacing:.5px;margin-bottom:8px}
.fcol li{list-style:none;font-size:12px;line-height:24px;color:#ccc}
.social{display:flex;gap:22px;margin-top:12px}
.social span{width:15px;height:15px;border-radius:50%;background:#ccc;display:block}
</style>
</head>
<body>

<div class="top-rule"></div>

<header class="header">
  <div class="abs contact-line">
    <svg viewBox="0 0 24 24"><path d="M6.6 10.8a15 15 0 0 0 6.6 6.6l2.2-2.2c.3-.3.7-.4 1-.2 1.1.4 2.3.6 3.6.6.6 0 1 .4 1 1V20c0 .6-.4 1-1 1A17 17 0 0 1 3 4c0-.6.4-1 1-1h3.5c.6 0 1 .4 1 1 0 1.3.2 2.5.6 3.6.1.3 0 .7-.2 1z"/></svg>
    <span>123-456-7890</span><span class="sep">|</span>
    <svg viewBox="0 0 24 24"><path d="M2 5h20v14H2z M2 5l10 8 10-8" /></svg>
    <span>info@companyname.com</span>
  </div>
  <div class="abs brand">Brenwick Structures</div>
  <div class="abs search"><span>Search..</span>
    <svg viewBox="0 0 24 24" fill="none" stroke="#d3302a" stroke-width="3"><circle cx="10" cy="10" r="7"/><path d="M15 15l6 6"/></svg>
  </div>
</header>

<nav class="nav">
  <a href="#">HOME</a><a href="#">PORTFOLIO</a><a href="#">PRODUCT SPECS</a><a href="#">TESTIMONIALS</a><a href="#">OUR PROCESS</a><a href="#">CONTACT</a>
</nav>

<section class="hero">
  <div class="hero-photo" role="img" aria-label="Photo of a construction manager in a hard hat with his team in front of a city skyline"></div>
  <h1 class="abs hero-title">BUILDING DREAMS,<br>SO YOU CAN BUILD MEMORIES</h1>
  <p class="abs hero-sub">Duis aliquam nibh a dui iaculis viverra id a velit.</p>
  <a class="abs btn btn-red" href="#">READ MORE</a>
</section>

<h2 class="abs welcome-title">WELCOME TO BRENWICK STRUCTURES</h2>
<p class="abs welcome-text">Aliquam molestie, mi et imperdiet euismod, dui purus auctor tellus, et interdum lacus lectus et ante. Sed accumsan sollicitudin sapien, sit amet adipiscing turpis gravida ac. In congue, neque ac lobortis volutpat, libero mauris varius mi, vitae suscipit ipsum ligula vitae risus. Duis aliquam nibh a dui iaculis viverra id a velit. Vivamus egestas risus in magna varius commodo. Sed semper viverra egestas.</p>
<div class="abs rule"></div>

<div class="abs tabs">
  <svg width="1051" height="54" viewBox="0 0 1051 54">
    <rect x="455" y="0" width="596" height="54" fill="#1a93cb"/>
    <polygon points="0,0 497,0 524,27 497,54 0,54" fill="#4a4a4a"/>
  </svg>
  <span class="tab-label" style="left:0;width:490px;text-align:center">COMMERCIAL CONSTRUCTION</span>
  <span class="tab-label" style="left:524px;width:527px;text-align:center">RESIDENTIAL BUILDINGS</span>
</div>
<div class="abs service-box"></div>
<div class="abs service-photo" role="img" aria-label="Photo of a concrete commercial building under construction with a tower crane"></div>
<h3 class="abs service-title">COMMERCIAL CONSTRUCTION</h3>
<p class="abs service-text">Aliquam molestie, mi et imperdiet euismod, dui purus auctor tellus, et interdum lacus lectus et ante. Sed accumsan sollicitudin sapien, sit amet adipiscing turpis gravida ac. In congue, neque ac lobortis volutpat, libero mauris varius mi, vitae suscipit ipsum ligula vitae risus. Duis aliquam nibh a dui iaculis viverra id a velit. Vivamus egestas risus in magna varius commodo. Sed semper viverra egestas.</p>
<a class="abs btn btn-blue service-btn" href="#">READ MORE</a>

<section class="abs updates"></section>
<h2 class="abs sec-title blog-title">BLOG POSTS</h2>
<article class="post" style="left:75px">
  <div class="post-photo" role="img" aria-label="Photo of workers tying rebar on a site" style="background:linear-gradient(#6d6a66,#3c3935)"></div>
  <h3>AENEAN A NIBH EGET TURPIS<br>VEHICULA TEMPUS...</h3>
  <p>Duis aliquam nibh a dui iaculis viverra id a velit. Vivamus egestas risus in magna varius commodo...</p>
  <a class="more" href="#">READ MORE</a>
</article>
<article class="post" style="left:331px">
  <div class="post-photo" role="img" aria-label="Photo of a modern glass office building at dusk" style="background:linear-gradient(#1e4fa8,#3a72c4 60%,#8a7a5a)"></div>
  <h3>AENEAN A NIBH EGET TURPIS<br>VEHICULA TEMPUS...</h3>
  <p>Duis aliquam nibh a dui iaculis viverra id a velit. Vivamus egestas risus in magna varius commodo...</p>
  <a class="more" href="#">READ MORE</a>
</article>
<article class="post" style="left:586px">
  <div class="post-photo" role="img" aria-label="Photo of a team reviewing building plans" style="background:linear-gradient(#e4e7ea,#9aa3ad)"></div>
  <h3>AENEAN A NIBH EGET TURPIS<br>VEHICULA TEMPUS...</h3>
  <p>Duis aliquam nibh a dui iaculis viverra id a velit. Vivamus egestas risus in magna varius commodo...</p>
  <a class="more" href="#">READ MORE</a>
</article>
<div class="abs divider"></div>
<h2 class="abs sec-title news-title">NEWS</h2>
<div class="news-item" style="top:1462px"><div class="date">NOV 20, 2015</div><p>Duis aliquam nibh a dui iaculis viverra id a velit. Vivamus egestas risus..</p><a class="more" href="#">READ MORE</a></div>
<div class="news-item" style="top:1570px"><div class="date">NOV 20, 2015</div><p>Duis aliquam nibh a dui iaculis viverra id a velit. Vivamus egestas risus..</p><a class="more" href="#">READ MORE</a></div>
<div class="news-item" style="top:1678px"><div class="date">NOV 20, 2015</div><p>Duis aliquam nibh a dui iaculis viverra id a velit. Vivamus egestas risus..</p><a class="more" href="#">READ MORE</a></div>

<h2 class="abs sec-title testi-title">TESTIMONIALS</h2>
<svg class="abs arrow" style="left:92px;top:1947px" viewBox="0 0 22 28"><path d="M16 4L6 14l10 10" fill="none" stroke="#555" stroke-width="4"/></svg>
<svg class="abs arrow" style="left:1083px;top:1947px" viewBox="0 0 22 28"><path d="M6 4l10 10L6 24" fill="none" stroke="#555" stroke-width="4"/></svg>
<div class="abs testi-photo" role="img" aria-label="Portrait photo of a satisfied client"></div>
<p class="abs testi-quote"><span class="qm">&ldquo;</span> Aliquam molestie, mi et imperdiet euismod, dui purus auctor tellus, et interdum lacus lectus et ante. Sed accumsan sollicitudin sapien, sit amet adipiscing turpis gravida ac. In congue, neque ac lobortis volutpat, libero mauris varius mi, vitae suscipit ipsum ligula vitae risus. Duis aliquam nibh a dui iaculis viverra id a velit. Vivamus egestas risus in magna varius commodo...<span class="qm">&rdquo;</span></p>
<div class="abs testi-name">-NAME GOSE HERE</div>

<footer class="abs footer"></footer>
<div class="abs footer-brand">Brenwick Structures</div>
<div class="abs footer-copy">Copyright © 2015. All Right Reserved<br>Terms of Services</div>
<div class="fcol" style="left:435px"><h4>COMPANY</h4><ul><li>Home</li><li>Portfolio</li><li>Product Specs</li><li>Testimonials</li><li>Our Process</li><li>Contact</li></ul></div>
<div class="fcol" style="left:612px"><h4>SERVICES</h4><ul><li>Commercial Construction</li><li>Residential Buildings</li></ul></div>
<div class="fcol" style="left:817px"><h4>CONNECT US</h4><div class="social"><span></span><span></span><span></span><span></span><span></span><span></span></div></div>

</body>
</html>
```